Four in One (Flexible infographic for Content Management Industry)

See attachment.
A graphic depicting 4 products, where each can stand on its own and each can be combined with others, but where, if all are taken together, the best result is achieved (the "super product").
Intended use is web. See attached file as an example.
The most basic idea is as the attached diagram shows, where 4 rectangles are arranged in a quadrangle, with a middle rectangle in the center representing the combined 4 products. This concept is fine except it is a bit too obvious as it stands. We are looking for either a variation of this or another concept.
The audience is technical + professional + enterprise - NOT consumers. Hence the design should be conservative in nature.
We are aware of tools like as Canva or Pictogram where such graphics are available, but we are looking for something with a bit more imagination and flexibility.
This graphic should be targeted to web sites and be delivered with vector-based (SVG) graphics.

```html
<!DOCTYPE html>
<html lang="en">
<head>
<meta charset="utf-8">
<title>Four in One – Super Product</title>
<link rel="stylesheet" href="https://fonts.googleapis.com/css2?family=Poppins:wght@400;500;700;800&display=swap">
<style>
  :root {
    --navy: #0d1629;
    --slate: #1f2536;
    --white: #ffffff;
    --yellow: #f5a90f;
    --red: #e3171b;
    --green: #57931f;
    --blue: #3658b5;
    --ink: #0b0b0b;
  }
  * { box-sizing: border-box; margin: 0; padding: 0; }
  html, body { width: 1200px; height: 956px; overflow: hidden; background: var(--white); }
  body { position: relative; font-family: "Poppins", sans-serif; color: var(--white); }

  .card {
    position: absolute;
    width: 494px;
    height: 307px;
    box-shadow: 8px 12px 18px rgba(0,0,0,0.35);
  }
  .card--documents { left: 86px; top: 156px; background: var(--navy); border-radius: 0 56px 0 56px; }
  .card--security  { left: 619px; top: 156px; background: var(--slate); border-radius: 56px 0 56px 0; }
  .card--erp       { left: 86px; top: 493px; background: var(--slate); border-radius: 56px 0 56px 0; }
  .card--digital   { left: 619px; top: 493px; background: var(--navy); border-radius: 0 56px 0 56px; }

  .card__title {
    position: absolute;
    font-size: 25px;
    line-height: 25px;
    font-weight: 500;
    letter-spacing: 0.2px;
    white-space: nowrap;
  }
  .card__title strong { display: block; font-weight: 800; }
  .card__lead {
    position: absolute;
    font-size: 14.7px;
    line-height: 17.5px;
    font-weight: 700;
    white-space: nowrap;
  }
  .card__list { position: absolute; list-style: none; font-size: 13.7px; line-height: 20px; white-space: nowrap; }
  .card__list li { display: flex; align-items: center; gap: 6px; }
  .tick { width: 13px; height: 13px; flex: none; }

  .card__button {
    position: absolute;
    width: 133px;
    height: 34px;
    border-radius: 17px;
    font-size: 15px;
    font-weight: 700;
    line-height: 34px;
    text-align: center;
  }
  .card__icon { position: absolute; fill: none; stroke-width: 2; stroke-linejoin: round; stroke-linecap: round; }

  .is-left .card__title, .is-left .card__lead, .is-left .card__list { left: 53px; }
  .is-left .card__button { left: 51px; }
  .is-right .card__title, .is-right .card__lead, .is-right .card__list { right: 53px; text-align: right; }
  .is-right .card__list li { justify-content: flex-end; }
  .is-right .card__button { right: 53px; }

  .card--documents .card__title strong { color: var(--yellow); }
  .card--documents .tick circle { fill: var(--yellow); }
  .card--documents .card__button { background: var(--yellow); color: var(--navy); }
  .card--documents .card__icon { stroke: var(--yellow); }

  .card--security .card__title strong { color: var(--red); }
  .card--security .tick circle { fill: var(--red); }
  .card--security .card__button { background: var(--red); color: var(--white); }
  .card--security .card__icon { stroke: var(--red); }

  .card--erp .card__title strong { color: var(--green); }
  .card--erp .tick circle { fill: var(--green); }
  .card--erp .card__button { background: var(--green); color: var(--white); }
  .card--erp .card__icon { stroke: var(--green); }

  .card--digital .card__title strong { color: var(--blue); }
  .card--digital .tick circle { fill: var(--blue); }
  .card--digital .card__button { background: var(--blue); color: var(--white); }
  .card--digital .card__icon { stroke: var(--blue); }

  .hub-halo {
    position: absolute; left: 491px; top: 364px; width: 216px; height: 216px;
    border-radius: 50%; background: rgba(225,225,225,0.22);
  }
  .hub {
    position: absolute; left: 511px; top: 384px; width: 176px; height: 176px;
    border-radius: 50%; background: var(--yellow);
    box-shadow: 6px 10px 18px rgba(0,0,0,0.35);
    display: flex; align-items: center; justify-content: center; text-align: center;
  }
  .hub__label {
    font-size: 29px; line-height: 26px; font-weight: 800; color: var(--ink);
    -webkit-text-stroke: 4px var(--white); paint-order: stroke fill;
    letter-spacing: -0.3px;
  }
</style>
</head>
<body>

<section class="card card--documents is-left">
  <h2 class="card__title" style="top:30px">DOCUMENT<strong>MANAGEMENT</strong></h2>
  <p class="card__lead" style="top:101px">Streamline document organization, access, &amp;<br>collaboration with easier</p>
  <ul class="card__list" style="top:146px">
    <li><svg class="tick" viewBox="0 0 14 14"><circle cx="7" cy="7" r="7"/><path d="M3.8 7.2l2.2 2.2 4.2-4.4" stroke="#fff" stroke-width="1.8" fill="none"/></svg>Centralized Document Control</li>
    <li><svg class="tick" viewBox="0 0 14 14"><circle cx="7" cy="7" r="7"/><path d="M3.8 7.2l2.2 2.2 4.2-4.4" stroke="#fff" stroke-width="1.8" fill="none"/></svg>Collaborative Workspace Integration</li>
    <li><svg class="tick" viewBox="0 0 14 14"><circle cx="7" cy="7" r="7"/><path d="M3.8 7.2l2.2 2.2 4.2-4.4" stroke="#fff" stroke-width="1.8" fill="none"/></svg>Automated Compliance Tracking</li>
  </ul>
  <svg class="card__icon" style="left:375px;top:190px" width="64" height="60" viewBox="0 0 64 60" aria-hidden="true">
    <rect x="2" y="4" width="16" height="22"/><rect x="20" y="1" width="24" height="26"/><rect x="46" y="4" width="16" height="22"/>
    <rect x="24" y="6" width="10" height="8"/><path d="M5 10h9M5 16h9M49 10h9M49 16h9"/>
    <path d="M4 24h20l4 5h32v29H4z"/><rect x="21" y="38" width="22" height="9"/>
  </svg>
  <div class="card__button" style="top:241px">LEARN MORE</div>
</section>

<section class="card card--security is-right">
  <h2 class="card__title" style="top:30px">SECURITY &amp;<strong>COMPLIANCE</strong></h2>
  <p class="card__lead" style="top:101px">Benefit from tailored cloud solutions, secure data<br>storage, and expert disaster recovery planning for<br>reliable and scalable IT operations</p>
  <ul class="card__list" style="top:162px">
    <li>Custom Cloud Solutions<svg class="tick" viewBox="0 0 14 14"><circle cx="7" cy="7" r="7"/><path d="M3.8 7.2l2.2 2.2 4.2-4.4" stroke="#fff" stroke-width="1.8" fill="none"/></svg></li>
    <li>Secure Data Storage<svg class="tick" viewBox="0 0 14 14"><circle cx="7" cy="7" r="7"/><path d="M3.8 7.2l2.2 2.2 4.2-4.4" stroke="#fff" stroke-width="1.8" fill="none"/></svg></li>
    <li>Expert Disaster Recovery<svg class="tick" viewBox="0 0 14 14"><circle cx="7" cy="7" r="7"/><path d="M3.8 7.2l2.2 2.2 4.2-4.4" stroke="#fff" stroke-width="1.8" fill="none"/></svg></li>
  </ul>
  <svg class="card__icon" style="left:57px;top:194px" width="56" height="56" viewBox="0 0 56 56" aria-hidden="true">
    <rect x="2" y="22" width="52" height="32" rx="3"/><path d="M2 32h52"/>
    <path d="M28 3l13 5v10c0 9-6 15-13 19-7-4-13-10-13-19V8z"/><circle cx="28" cy="17" r="5"/>
    <rect x="7" y="40" width="10" height="7"/><rect x="28" y="41" width="20" height="5" rx="2.5"/>
    <path d="M15 9H6v6M41 9h9v6"/><circle cx="5" cy="16" r="1.6"/><circle cx="51" cy="16" r="1.6"/>
  </svg>
  <div class="card__button" style="top:241px">LEARN MORE</div>
</section>

<section class="card card--erp is-left">
  <h2 class="card__title" style="top:35px">ENTERPRISE<strong>RESOURCE PLANNING</strong></h2>
  <p class="card__lead" style="top:105px">Simplify management across finance, sales, &amp;<br>operations, enabling better decision-making &amp;<br>improved productivity.</p>
  <ul class="card__list" style="top:165px">
    <li><svg class="tick" viewBox="0 0 14 14"><circle cx="7" cy="7" r="7"/><path d="M3.8 7.2l2.2 2.2 4.2-4.4" stroke="#fff" stroke-width="1.8" fill="none"/></svg>Integrated Business Processes</li>
    <li><svg class="tick" viewBox="0 0 14 14"><circle cx="7" cy="7" r="7"/><path d="M3.8 7.2l2.2 2.2 4.2-4.4" stroke="#fff" stroke-width="1.8" fill="none"/></svg>Enhanced Decision-Making</li>
    <li><svg class="tick" viewBox="0 0 14 14"><circle cx="7" cy="7" r="7"/><path d="M3.8 7.2l2.2 2.2 4.2-4.4" stroke="#fff" stroke-width="1.8" fill="none"/></svg>Productivity Improvement</li>
  </ul>
  <svg class="card__icon" style="left:376px;top:208px" width="64" height="64" viewBox="0 0 64 64" aria-hidden="true">
    <rect x="2" y="6" width="24" height="12"/>
    <circle cx="53" cy="11" r="9"/><circle cx="42" cy="32" r="9"/><circle cx="53" cy="52" r="9"/>
    <path d="M26 12h18M36 12v40h8M30 32h3"/>
    <path d="M10 62V46l-4-4v-8l4 3V24a2.5 2.5 0 015 0v12l9 2v10l-4 6v8"/>
  </svg>
  <div class="card__button" style="top:244px">LEARN MORE</div>
</section>

<section class="card card--digital is-right">
  <h2 class="card__title" style="top:35px">DIGITAL<strong>TRANSFORMATION</strong></h2>
  <p class="card__lead" style="top:105px">Turn scanned documents into easily searchable<br>digital archives, boosting efficiency &amp; accessibility</p>
  <ul class="card__list" style="top:149px">
    <li>Instant searchable Archives with OCR<svg class="tick" viewBox="0 0 14 14"><circle cx="7" cy="7" r="7"/><path d="M3.8 7.2l2.2 2.2 4.2-4.4" stroke="#fff" stroke-width="1.8" fill="none"/></svg></li>
    <li>Automated Document Classification<svg class="tick" viewBox="0 0 14 14"><circle cx="7" cy="7" r="7"/><path d="M3.8 7.2l2.2 2.2 4.2-4.4" stroke="#fff" stroke-width="1.8" fill="none"/></svg></li>
    <li>Korrindale and Cloud Blob Ready<svg class="tick" viewBox="0 0 14 14"><circle cx="7" cy="7" r="7"/><path d="M3.8 7.2l2.2 2.2 4.2-4.4" stroke="#fff" stroke-width="1.8" fill="none"/></svg></li>
  </ul>
  <svg class="card__icon" style="left:48px;top:212px" width="64" height="60" viewBox="0 0 64 60" aria-hidden="true">
    <rect x="2" y="2" width="60" height="42"/><path d="M2 8h30M2 38h60M28 44v8M36 44v8M20 56h24v-4H20z"/>
    <path d="M8 34v-4M14 34v-9M20 34v-14M26 34V14"/>
    <path d="M38 14h8l4-4h6M38 20h14M38 26h6l4 4h8"/><circle cx="57" cy="10" r="1.8"/><circle cx="57" cy="30" r="1.8"/>
  </svg>
  <div class="card__button" style="top:244px">LEARN MORE</div>
</section>

<div class="hub-halo"></div>
<div class="hub"><p class="hub__label">Super<br>Product</p></div>

</body>
</html>
```